Design a Website in Wordpress for an Australian Health Training Company in Health related courses

We require a WORDPRESS based Website (due to add on's we need to use for third party software) to replace our old site.
We offer national face to face delivery in medical reception, terminology and also administration.
The website will have around 6 pages and the ability to describe our main 6 courses (perhaps on the Courses page this may be tabs opening up to details for example?)
I have attached a previous sample of a Joomla site which was being developed (please do not feel you have to copy this - but I am just giving it as a sample - copying would be boring). But it gives an idea of look/feel and colours which may be suitable. Open to other ideas though.
I will provide some of the content, but would like the ability to finish the content myself.
Images and graphics are important. While a few medical photos re great - don't be tempted to us all pictures of doctors and nurses (although a couple would be good) - these are administrative courses so general corporate, eye catching visionary pictures of people in general are great. A medical type picture is also fine.
THE BOOKING system - will be via an ADD ON which will occur at the end of the project and is supplied by a third party software company (our student management system). This project will include up to 2 hours working with the Tech guys from the third party software to enable the ADD ON. If this ADD ON requires more time, we will pay hourly (although I do not expect it will).
Target Market(s)
Mostly a female market, many mature aged women target 25-45 yrs. Mixture of medical/health and corporate. Maybe a bit of mums returning to work and corporate inspiration.
Industry/Entity Type
It Company
Coding
Coded - Design and coding required
Number of Pages Required
5+ page
Requirements
Must have
- Wordpress
- Great graphics
- Interesting
- professional and clean
- Enquiry section (info Pak)
- Should have a University feel to it - Education
- Pages
- Home Page - About Us - Recruitment -Courses - Class Schedule - Traineeships Queensland Funding - Latest News Blog - Corporate Training- Contact us

```html
<!DOCTYPE html>
<html lang="en">
<head>
<meta charset="utf-8">
<title>Harwell Institute of Training</title>
<link rel="stylesheet" href="https://fonts.googleapis.com/css2?family=Cinzel:wght@400;600;700&family=Open+Sans:ital,wght@0,400;0,600;0,700;1,400&display=swap">
<style>
:root{
  --navy:#2c4466;
  --navy-dark:#1f3350;
  --orange:#e8913a;
  --orange-light:#f0a856;
  --ink:#2b2b2b;
  --muted:#6b6f75;
  --pale:#e8ecf2;
  --white:#ffffff;
  --grey-btn:#d9dbde;
  --head:'Cinzel', Georgia, serif;
  --body:'Open Sans', Arial, sans-serif;
}
*{box-sizing:border-box;margin:0;padding:0}
html,body{width:1200px;height:2390px;overflow:hidden}
body{position:relative;font-family:var(--body);color:var(--ink);background:var(--white)}
.abs{position:absolute}
svg{display:block}

/* top bar */
.topbar{left:0;top:0;width:1200px;height:45px;background:var(--navy-dark)}
.top-phone{left:518px;top:10px;display:flex;align-items:center;gap:8px;color:var(--white);font-weight:700;font-size:16px}
.top-phone .ic{width:26px;height:26px;border:2px solid var(--white);border-radius:50%;display:flex;align-items:center;justify-content:center}
.top-login{left:673px;top:6px;width:156px;height:33px;background:#243a5a;color:var(--white);font-size:12px;font-weight:700;display:flex;align-items:center;justify-content:center;gap:7px}
.top-btn{top:6px;height:32px;border-radius:3px;font-size:12px;font-weight:700;display:flex;align-items:center;justify-content:center;gap:6px}
.btn-enroll{left:853px;width:119px;background:var(--grey-btn);color:var(--navy-dark)}
.btn-info{left:980px;width:120px;background:var(--orange);color:var(--white)}

/* nav */
.nav{left:0;top:45px;width:1200px;height:67px;background:var(--white)}
.nav-list{left:308px;top:62px;display:flex;gap:21px;list-style:none;font-size:13px;line-height:17px;color:#444}
.nav-list li.active{color:var(--orange)}
.nav-search{left:1086px;top:71px}
.brand-badge{left:74px;top:0;width:180px;height:178px;border-radius:50%;background:var(--white);box-shadow:0 2px 6px rgba(0,0,0,.12);display:flex;flex-direction:column;align-items:center;justify-content:center;gap:10px}
.brand-badge .dot{width:46px;height:46px;border-radius:50%;background:var(--navy)}
.brand-name{font-family:var(--head);font-weight:700;color:var(--navy);font-size:15px;line-height:17px;text-align:center}

/* hero */
.hero-img{left:0;top:112px;width:1200px;height:427px;background:linear-gradient(180deg,#4f86c6 0%,#8fb4dc 45%,#6f8aa6 70%,#2f4e63 100%)}
.hero-title{left:96px;top:368px;font-family:var(--head);font-weight:600;font-size:32px;color:var(--white);letter-spacing:1px}
.hero-sub{left:97px;top:412px;font-size:19px;font-weight:600;color:var(--white)}
.hero-dots{left:523px;top:487px;display:flex;gap:6px}
.hero-dots span{width:34px;height:5px;border-radius:3px;background:var(--white)}
.hero-dots span.on{background:var(--orange)}

.enquiry{left:760px;top:115px;width:340px;height:424px;background:rgba(24,40,64,.88)}
.enquiry h2{position:absolute;left:0;top:12px;width:340px;text-align:center;font-family:var(--head);font-weight:400;font-size:22px;color:var(--white);letter-spacing:1px}
.enquiry label{position:absolute;left:21px;font-size:12px;color:var(--white)}
.enquiry .field{position:absolute;left:104px;width:217px;height:32px;background:var(--white)}
.enquiry .select-arrow{position:absolute;right:0;top:0;width:22px;height:32px;background:#eee;display:flex;align-items:center;justify-content:center}
.enquiry .submit{position:absolute;left:21px;top:350px;width:300px;height:50px;background:var(--orange);color:var(--white);font-weight:700;font-size:15px;display:flex;align-items:center;justify-content:center;border-radius:2px}

/* courses */
.section-title{position:absolute;font-family:var(--head);font-size:26px;color:var(--ink);letter-spacing:1px;text-align:center}
.courses-title{left:0;top:584px;width:1200px}
.course{position:absolute;top:640px;width:250px;text-align:center}
.course .ring{width:120px;height:120px;margin:0 auto;border:3px solid var(--navy);border-radius:50%;display:flex;align-items:center;justify-content:center}
.course h3{margin-top:16px;font-family:var(--head);font-weight:600;font-size:15px;line-height:20px;color:var(--ink)}
.course p{margin-top:12px;font-size:11.5px;line-height:22px;color:var(--muted);padding:0 6px}
.read-more{color:var(--orange);font-weight:700;font-size:12px;margin-top:10px;display:block}
.slide-arrow{position:absolute}

/* welcome + news */
.mid{left:0;top:963px;width:1200px;height:435px;background:var(--pale)}
.mid-title{position:absolute;font-family:var(--head);font-weight:400;font-size:23px;color:var(--ink);letter-spacing:0;white-space:nowrap}
.welcome-photo{left:99px;top:1070px;width:223px;height:149px;border:4px solid var(--white);background:linear-gradient(135deg,#c7a47a,#e8d8c2 55%,#9aa9b8);box-shadow:0 1px 3px rgba(0,0,0,.15)}
.welcome-text{left:343px;top:1066px;width:250px;font-size:12px;line-height:22px;color:var(--muted)}
.welcome-full{left:97px;top:1272px;width:500px;font-size:12px;line-height:22px;color:var(--muted)}
.post{position:absolute;left:622px;width:500px;height:120px}
.post .thumb{position:absolute;left:0;top:0;width:111px;height:100px;border:4px solid var(--white);box-shadow:0 1px 3px rgba(0,0,0,.15);background:linear-gradient(135deg,#b9c9da,#e9eef4 60%,#8fa4ba)}
.post h4{position:absolute;left:138px;top:2px;font-size:13.5px;font-weight:700;color:var(--ink);white-space:nowrap}
.post .date{position:absolute;left:138px;top:26px;font-size:12px;color:var(--ink);display:flex;gap:8px;align-items:center}
.post p{position:absolute;left:138px;top:53px;width:345px;font-size:12px;line-height:21px;color:var(--muted)}
.post-rule{left:622px;width:480px;height:1px;background:#cfd5dd}
.orange-link{position:absolute;color:var(--orange);font-weight:700;font-size:12px}

/* why */
.why{left:0;top:1398px;width:1200px;height:375px;background:linear-gradient(90deg,#e39a52 0%,#eea55c 45%,#e59448 100%)}
.why-title{left:0;top:1444px;width:1200px;font-family:var(--head);font-size:25px;color:var(--white);text-align:center;letter-spacing:1px}
.reason{position:absolute;top:1510px;width:200px;text-align:center;color:var(--white)}
.reason svg{margin:0 auto;height:60px}
.reason h3{margin-top:16px;font-family:var(--head);font-weight:400;font-size:15.5px;letter-spacing:0;white-space:nowrap}
.reason p{margin:10px auto 0;width:185px;font-size:12px;line-height:23px}

/* testimonials */
.testi-title{left:0;top:1814px;width:1200px}
.quote-circle{left:134px;top:1878px;width:118px;height:118px;border-radius:50%;background:#a9b2be}
.quote-circle span{position:absolute;left:18px;top:-6px;font-family:Georgia,serif;font-size:110px;color:#d7dce2;line-height:1}
.person-circle{left:210px;top:1871px;width:128px;height:128px;border-radius:50%;background:linear-gradient(160deg,#d8dde3,#9aa5b3);border:3px solid var(--white)}
.testi-text{left:376px;top:1880px;width:720px;font-style:italic;font-size:13.5px;line-height:30px;color:var(--muted)}
.testi-name{left:377px;top:1976px;font-family:var(--head);font-weight:600;font-size:16px;color:var(--ink)}

/* footer */
.footer{left:0;top:2064px;width:1200px;height:326px;background:var(--navy);border-top:4px solid var(--orange)}
.foot-brand{left:72px;top:2100px;width:240px;display:flex;flex-direction:column;align-items:center;gap:16px}
.foot-brand .brand-name{color:var(--white);font-size:18px;line-height:21px;font-weight:600;white-space:nowrap}
.foot-brand .dot{width:90px;height:90px;border-radius:50%;background:#3b5880}
.foot-h{position:absolute;top:2097px;font-family:var(--head);font-weight:400;font-size:17px;color:var(--white)}
.foot-links{left:360px;top:2142px;list-style:none;font-size:12px;line-height:18.8px;color:#dfe6ef}
.foot-text{position:absolute;font-size:12px;line-height:21px;color:#dfe6ef}
.news-input{left:598px;top:2195px;width:263px;height:33px;background:var(--white);font-size:11.5px;color:#666;padding:9px 12px}
.news-btn{left:598px;top:2249px;width:100px;height:37px;border:2px solid var(--white);border-radius:3px;color:var(--white);font-size:12px;font-weight:700;display:flex;align-items:center;justify-content:center}
.contact-row{position:absolute;left:909px;display:flex;gap:16px;font-size:12px;line-height:21px;color:#dfe6ef}
.foot-rule{left:0;top:2327px;width:1200px;height:1px;background:rgba(255,255,255,.12)}
.copyright{left:99px;top:2347px;font-size:12px;color:#dfe6ef}
.social{left:949px;top:2340px;display:flex;gap:7px}
.social span{width:34px;height:34px;border:2px solid var(--white);border-radius:50%}
</style>
</head>
<body>

<!-- top bar -->
<div class="abs topbar"></div>
<div class="abs top-phone">
  <span class="ic"><svg width="12" height="12" viewBox="0 0 24 24"><path fill="#fff" d="M6.6 10.8c1.4 2.8 3.8 5.1 6.6 6.6l2.2-2.2c.3-.3.7-.4 1-.2 1.1.4 2.3.6 3.6.6.6 0 1 .4 1 1V20c0 .6-.4 1-1 1C10.6 21 3 13.4 3 4c0-.6.4-1 1-1h3.5c.6 0 1 .4 1 1 0 1.3.2 2.5.6 3.6.1.3 0 .7-.2 1z"/></svg></span>
  08 5550 3817
</div>
<div class="abs top-login">
  <svg width="10" height="12" viewBox="0 0 10 12"><rect x="0" y="5" width="10" height="7" fill="#fff"/><path d="M2 5V3.5a3 3 0 0 1 6 0V5" fill="none" stroke="#fff" stroke-width="1.6"/></svg>
  STUDENT LOGIN
</div>
<div class="abs top-btn btn-enroll">
  <svg width="13" height="13" viewBox="0 0 14 14"><circle cx="7" cy="7" r="7" fill="#1f3350"/><path d="M4 7h6M7.5 4.5 10 7l-2.5 2.5" stroke="#fff" stroke-width="1.6" fill="none"/></svg>
  ENROLL NOW
</div>
<div class="abs top-btn btn-info">
  <svg width="13" height="13" viewBox="0 0 14 14"><circle cx="7" cy="7" r="7" fill="#fff"/><rect x="6" y="6" width="2" height="5" fill="#e8913a"/><circle cx="7" cy="4" r="1.1" fill="#e8913a"/></svg>
  INFO PACK
</div>

<!-- nav -->
<div class="abs nav"></div>
<ul class="abs nav-list">
  <li class="active">Home<br>Page</li>
  <li>About<br>Us</li>
  <li>Recruitment</li>
  <li>Courses</li>
  <li>Class<br>Schedule</li>
  <li>Traineeships<br>Queensland Funding</li>
  <li>Latest<br>News Blog</li>
  <li>Corporate<br>Training</li>
  <li>Contact<br>Us</li>
</ul>
<svg class="abs nav-search" width="18" height="18" viewBox="0 0 18 18"><circle cx="7.5" cy="7.5" r="5.5" fill="none" stroke="#444" stroke-width="2.2"/><path d="M11.5 11.5 16.5 16.5" stroke="#444" stroke-width="2.6"/></svg>

<!-- hero -->
<div class="abs hero-img" role="img" aria-label="City skyline with harbour and tall office towers under a blue sky"></div>
<div class="abs hero-title">HARWELL INSTITUTE OF TRAINING</div>
<div class="abs hero-sub">We are a Health Training Company in Australia</div>
<div class="abs hero-dots"><span class="on"></span><span></span><span></span><span></span></div>

<div class="abs brand-badge">
  <span class="dot"></span>
  <div class="brand-name">HARWELL INSTITUTE<br>OF TRAINING</div>
</div>

<form class="abs enquiry">
  <h2>EMAIL me an Info Pack</h2>
  <label style="top:86px">Name :</label><div class="field" style="top:78px"></div>
  <label style="top:140px">Email :</label><div class="field" style="top:132px"></div>
  <label style="top:194px">Course :</label><div class="field" style="top:186px"><span class="select-arrow"><svg width="8" height="5" viewBox="0 0 8 5"><path d="M0 0h8L4 5z" fill="#777"/></svg></span></div>
  <label style="top:248px">State :</label><div class="field" style="top:240px"></div>
  <label style="top:303px">Mobile :</label><div class="field" style="top:295px"></div>
  <div class="submit">MAKE AN ENQUIRY</div>
</form>

<!-- courses -->
<h2 class="section-title courses-title">LIST OF COURSES</h2>
<svg class="slide-arrow" style="left:50px;top:752px" width="12" height="22" viewBox="0 0 12 22"><path d="M11 1 1 11l10 10" fill="none" stroke="#999" stroke-width="2"/></svg>
<svg class="slide-arrow" style="left:1136px;top:752px" width="12" height="22" viewBox="0 0 12 22"><path d="M1 1l10 10L1 21" fill="none" stroke="#999" stroke-width="2"/></svg>

<div class="course" style="left:84px">
  <div class="ring"><svg width="56" height="50" viewBox="0 0 56 50"><path d="M20 8V4h16v4" fill="none" stroke="#2c4466" stroke-width="4"/><rect x="2" y="8" width="52" height="40" rx="5" fill="#2c4466"/><circle cx="28" cy="28" r="13" fill="#fff"/><path d="M28 20v16M20 28h16" stroke="#2c4466" stroke-width="5"/></svg></div>
  <h3>MEDICAL RECEPTION<br>&amp; TERMINOLOGY</h3>
  <p>Our course material and unique training programme is developed in conjunction with Industry to reflect</p>
  <span class="read-more">READ MORE &gt;&gt;</span>
</div>
<div class="course" style="left:345px">
  <div class="ring"><svg width="64" height="56" viewBox="0 0 64 56"><circle cx="20" cy="18" r="12" fill="none" stroke="#2c4466" stroke-width="7" stroke-dasharray="5 3.4"/><circle cx="20" cy="18" r="5" fill="#2c4466"/><rect x="24" y="22" width="36" height="32" rx="2" fill="#fff" stroke="#2c4466" stroke-width="3"/><path d="M29 31l3 3 4-5M29 42l3 3 4-5" fill="none" stroke="#2c4466" stroke-width="2.4"/><path d="M40 32h15M40 43h15" stroke="#2c4466" stroke-width="3"/></svg></div>
  <h3>CERT III BUSINESS<br>ADMINISTRATION</h3>
  <p>Our course material and unique training programme is developed in conjunction with Industry to reflect</p>
  <span class="read-more">READ MORE &gt;&gt;</span>
</div>
<div class="course" style="left:605px">
  <div class="ring"><svg width="62" height="54" viewBox="0 0 62 54"><path d="M31 52 7 28A13 13 0 0 1 31 9a13 13 0 0 1 24 19z" fill="#2c4466"/><path d="M2 28h18l5-9 6 18 6-13 3 4h20" fill="none" stroke="#fff" stroke-width="4"/><path d="M2 28h6M54 28h6" stroke="#2c4466" stroke-width="4"/></svg></div>
  <h3>MEDICAL<br>TERMINOLOGY</h3>
  <p>Our course material and unique training programme is developed in conjunction with Industry to reflect</p>
  <span class="read-more">READ MORE &gt;&gt;</span>
</div>
<div class="course" style="left:865px">
  <div class="ring"><svg width="62" height="54" viewBox="0 0 62 54"><path d="M31 20v-8c0-5 8-5 8-10" fill="none" stroke="#2c4466" stroke-width="3"/><rect x="2" y="20" width="58" height="32" rx="4" fill="#2c4466"/><g fill="#fff"><rect x="8" y="26" width="6" height="5"/><rect x="17" y="26" width="6" height="5"/><rect x="26" y="26" width="6" height="5"/><rect x="35" y="26" width="6" height="5"/><rect x="44" y="26" width="10" height="5"/><rect x="8" y="34" width="10" height="5"/><rect x="21" y="34" width="6" height="5"/><rect x="30" y="34" width="6" height="5"/><rect x="39" y="34" width="6" height="5"/><rect x="48" y="34" width="6" height="5"/><rect x="8" y="42" width="6" height="5"/><rect x="17" y="42" width="28" height="5"/><rect x="48" y="42" width="6" height="5"/></g></svg></div>
  <h3>KEYBOARD AND<br>TYPING</h3>
  <p>Our course material and unique training programme is developed in conjunction with Industry to reflect</p>
  <span class="read-more">READ MORE &gt;&gt;</span>
</div>

<!-- welcome + news -->
<div class="abs mid"></div>
<h2 class="mid-title" style="left:97px;top:1006px">WELCOME TO HARWELL INSTITUTE</h2>
<div class="abs welcome-photo" role="img" aria-label="Smiling professional woman at a desk, promoting student success"></div>
<p class="abs welcome-text">Harwell is Australia's Leading Provider of Educational, Training and Support Services for the Medical and Dental industry - enabling students to be immediately skilled and 'Job Ready' for a career in Health.<br><br>Harwell is a Registered Training Organisation offering specialised Medical Administration Training in over 15 locations</p>
<p class="abs welcome-full">Australia wide. Harwell have trained thousands of students the required knowledge and skills to become successful health care administrators.</p>
<span class="orange-link" style="left:98px;top:1335px">READ MORE &gt;&gt;</span>

<h2 class="mid-title" style="left:622px;top:1006px">LATEST NEWS BLOG</h2>
<div class="post" style="top:1068px">
  <div class="thumb" role="img" aria-label="Group of cheerful medical staff celebrating"></div>
  <h4>AT VERO EOS ET ACCUSAMUS ET IUSTO ODIO DIG</h4>
  <div class="date"><svg width="11" height="11" viewBox="0 0 11 11"><rect y="1.5" width="11" height="9.5" fill="#e8913a"/><rect x="1.5" y="4" width="8" height="5.5" fill="#fff"/></svg>05/03/2016</div>
  <p>Nemo enim ipsam voluptatem quia voluptas sit aspernatur aut odit aut fugit, sed quia consequuntur..</p>
</div>
<div class="abs post-rule" style="top:1188px"></div>
<div class="post" style="top:1208px">
  <div class="thumb" role="img" aria-label="Students working together in a classroom"></div>
  <h4>AT VERO EOS ET ACCUSAMUS ET IUSTO ODIO DIG</h4>
  <div class="date"><svg width="11" height="11" viewBox="0 0 11 11"><rect y="1.5" width="11" height="9.5" fill="#e8913a"/><rect x="1.5" y="4" width="8" height="5.5" fill="#fff"/></svg>05/03/2016</div>
  <p>Nemo enim ipsam voluptatem quia voluptas sit aspernatur aut odit aut fugit, sed quia consequuntur..</p>
</div>
<div class="abs post-rule" style="top:1325px"></div>
<span class="orange-link" style="left:622px;top:1335px">VIEW MORE &gt;&gt;</span>

<!-- why -->
<div class="abs why" role="img" aria-label="Warm orange-tinted background of students studying together"></div>
<h2 class="abs why-title">WHY HARWELL INSTITUTE ?</h2>
<div class="reason" style="left:83px">
  <svg width="60" height="60" viewBox="0 0 60 60"><rect x="4" y="26" width="12" height="30" fill="#fff"/><path d="M20 28 31 6c5 0 7 4 6 9l-2 9h16c4 0 6 4 5 7l-5 20c-1 3-3 5-6 5H20z" fill="#fff"/></svg>
  <h3>QUALITY</h3>
  <p>Harwell delivery quality, effective training facilitated by industry leaders. Just ask our students who rate us</p>
</div>
<div class="reason" style="left:284px">
  <svg width="60" height="60" viewBox="0 0 60 60"><path d="M30 3l8 18 19 2-14 13 4 19-17-10-17 10 4-19L3 23l19-2z" fill="#fff"/></svg>
  <h3>EXPERIENCE</h3>
  <p>Harwell is Australia's largest and leading providers of nationally recognised training inhealth administration</p>
</div>
<div class="reason" style="left:490px">
  <svg width="70" height="60" viewBox="0 0 70 60"><path d="M3 4v53h64" fill="none" stroke="#fff" stroke-width="4"/><g fill="#fff"><rect x="12" y="34" width="8" height="19"/><rect x="24" y="22" width="8" height="31"/><rect x="36" y="28" width="8" height="25"/><rect x="48" y="14" width="8" height="39"/></g></svg>
  <h3>VALUE</h3>
  <p>Our innovative teaching approach allows us to deliver exceptional training at affordable prices</p>
</div>
<div class="reason" style="left:698px;width:210px">
  <svg width="62" height="60" viewBox="0 0 62 60"><path d="M40 8H8v48h44V26" fill="none" stroke="#fff" stroke-width="5"/><path d="M22 42l3-11 25-25 8 8-25 25z" fill="#fff"/></svg>
  <h3>INDUSTRY RECOGNISED</h3>
  <p>Harwell work hand in hand with industry to develop our core programme and consolidate the programme</p>
</div>
<div class="reason" style="left:914px">
  <svg width="50" height="60" viewBox="0 0 50 60"><path d="M4 3h30l13 13v41H4z" fill="none" stroke="#fff" stroke-width="4"/><path d="M33 3v14h14" fill="none" stroke="#fff" stroke-width="4"/><path d="M12 28h26M12 37h26M12 46h26" stroke="#fff" stroke-width="3.5"/></svg>
  <h3>GREAT JOB RESULTS</h3>
  <p>Harwell students get jobs! Our focus is to create job-ready students who are mentored to achieve their goals.</p>
</div>

<!-- testimonials -->
<h2 class="section-title testi-title">TESTIMONIALS</h2>
<svg class="slide-arrow" style="left:50px;top:1924px" width="12" height="22" viewBox="0 0 12 22"><path d="M11 1 1 11l10 10" fill="none" stroke="#999" stroke-width="2"/></svg>
<svg class="slide-arrow" style="left:1136px;top:1924px" width="12" height="22" viewBox="0 0 12 22"><path d="M1 1l10 10L1 21" fill="none" stroke="#999" stroke-width="2"/></svg>
<div class="abs quote-circle"><span>&ldquo;</span></div>
<div class="abs person-circle" role="img" aria-label="Portrait of the graduate giving the testimonial"></div>
<p class="abs testi-text">I want to say a huge thank you for the course and knowledge I came away with. I have secured a fantastic job after my first application! Such good value for money too! I would highly recommend it. I'm a mature age person so it's never too late to up -skill yourself to get what you deserve!</p>
<div class="abs testi-name">JANE MERCER</div>

<!-- footer -->
<footer class="abs footer"></footer>
<div class="abs foot-brand">
  <div class="brand-name">HARWELL INSTITUTE<br>OF TRAINING</div>
  <span class="dot"></span>
</div>

<h3 class="foot-h" style="left:360px">INFORMATION</h3>
<ul class="abs foot-links">
  <li>Home</li><li>About Us</li><li>Recruitment</li><li>Courses</li><li>Class Schedule</li><li>Traineeships Queensland Funding</li><li>Latest News Blog</li><li>Corporate Training</li><li>Contact us</li>
</ul>

<h3 class="foot-h" style="left:598px">NEWSLETTER</h3>
<p class="foot-text" style="left:598px;top:2140px;width:230px">Register your email address to get information about us</p>
<div class="abs news-input">Email Address</div>
<div class="abs news-btn">SUBSCRIBE</div>

<h3 class="foot-h" style="left:909px">CONTACT US</h3>
<div class="contact-row" style="top:2141px">
  <svg width="11" height="15" viewBox="0 0 11 15" style="margin-top:3px"><path d="M5.5 0A5.5 5.5 0 0 0 0 5.5C0 9.5 5.5 15 5.5 15S11 9.5 11 5.5A5.5 5.5 0 0 0 5.5 0z" fill="#fff"/><circle cx="5.5" cy="5.5" r="2" fill="#2c4466"/></svg>
  <span>27 Kestrel Court, Suite 12,<br>QLD 4000 Brisbane</span>
</div>
<div class="contact-row" style="top:2210px">
  <svg width="13" height="13" viewBox="0 0 24 24" style="margin-top:4px"><path fill="#fff" d="M6.6 10.8c1.4 2.8 3.8 5.1 6.6 6.6l2.2-2.2c.3-.3.7-.4 1-.2 1.1.4 2.3.6 3.6.6.6 0 1 .4 1 1V20c0 .6-.4 1-1 1C10.6 21 3 13.4 3 4c0-.6.4-1 1-1h3.5c.6 0 1 .4 1 1 0 1.3.2 2.5.6 3.6.1.3 0 .7-.2 1z"/></svg>
  <span>08 5550 3817</span>
</div>
<div class="contact-row" style="top:2257px">
  <svg width="14" height="11" viewBox="0 0 14 11" style="margin-top:5px"><rect width="14" height="11" fill="#fff"/><path d="M0 0l7 6 7-6" fill="none" stroke="#2c4466" stroke-width="1.4"/></svg>
  <span>info@harwellhealth.com.au</span>
</div>

<div class="abs foot-rule"></div>
<div class="abs copyright">Copyrights &copy; 2016, Harwell Institute of Training. All rights reserved.</div>
<div class="abs social"><span></span><span></span><span></span><span></span></div>

</body>
</html>
```